Letterhead for a German Distribution/Manufacturing Company

We need a professional Letterhead in a unique Design.
not to playful.
The Letterhead has to show show that we are a international company with headquater in Germany.
all details like adress, Vat Tax Number, Bank Accout, Eori, email, Company number has to be on the Letterhead.
for example use: VAT TAX DE5470318 Bank Account: Kestrel Bank IBAN DE412058731ß204683 Swift: MORV0417352 EORI 3150428697 Company Number: HRB 51806 Adress: VOLMINTA UG Ahornweg 7 Postal Code 06384 City Lindenfeld Country: Germany Email: info@volminta-example.com
the design can be colored but doesnt have to be
Industry/Entity Type
Manufacturing and international distribution
Requirements
Must have
- show that we are a international company with headquater in Germany. our company infos and logo

```html
<!DOCTYPE html>
<html lang="en">
<head>
<meta charset="utf-8">
<title>VOLMINTA Letterhead</title>
<link rel="stylesheet" href="https://fonts.googleapis.com/css2?family=Poppins:wght@300;400;500;600&display=swap">
<style>
  :root {
    --canvas: #ffffff;
    --paper: #ffffff;
    --paper-tint: #f1f1f1;
    --ink: #262626;
    --ink-soft: #3a3a3a;
    --muted: #7a7a7a;
    --label: #8a8a8a;
    --rule: #4a4a4a;
    --flag-black: #1c1c1c;
    --flag-red: #d8232a;
    --flag-gold: #f2c400;
    --pin: #6b6b6b;
  }
  * { box-sizing: border-box; margin: 0; padding: 0; }
  html, body { width: 1200px; height: 2444px; overflow: hidden; background: var(--canvas); }
  body { font-family: "Poppins", sans-serif; color: var(--ink-soft); position: relative; }

  .letterhead {
    position: absolute; left: 35px; top: 491px; width: 1130px; height: 1461px;
    background: radial-gradient(ellipse at 55% 40%, var(--paper) 40%, var(--paper-tint) 100%);
    box-shadow: 0 10px 40px rgba(0,0,0,0.18);
    overflow: hidden;
  }

  .brand { position: absolute; left: 58px; top: 70px; display: flex; align-items: center; gap: 18px; }
  .brand-dot { width: 58px; height: 58px; border-radius: 50%; background: var(--ink); }
  .brand-name { font-size: 58px; font-weight: 400; color: var(--ink); letter-spacing: 0.5px; line-height: 1; }

  .hq { position: absolute; left: 610px; top: 78px; display: flex; align-items: center; gap: 30px; }
  .hq-pin { width: 54px; height: 76px; }
  .hq-text { font-size: 24px; font-weight: 500; color: var(--ink-soft); line-height: 28px; letter-spacing: 0.3px; }

  .rule { position: absolute; height: 2px; background: var(--rule); }
  .rule-top { left: 58px; width: 1015px; top: 190px; }
  .rule-foot { left: 58px; width: 841px; top: 1293px; }

  .salutation { position: absolute; left: 56px; top: 262px; font-size: 35px; font-weight: 500; color: var(--muted); }

  .letter-body { position: absolute; left: 58px; top: 343px; width: 1032px; font-size: 17.5px; font-weight: 300; line-height: 22px; color: var(--ink-soft); letter-spacing: -0.1px; }
  .letter-body p + p { margin-top: 22px; }

  .closing { position: absolute; left: 59px; top: 1006px; font-size: 18px; font-weight: 500; color: var(--ink); }
  .signature-mark { position: absolute; left: 60px; top: 1070px; width: 320px; height: 88px; background: linear-gradient(90deg, #ececec, #f7f7f7); border-radius: 4px; }
  .signature-line { position: absolute; left: 58px; top: 1164px; width: 351px; height: 2px; background: var(--rule); }
  .signature-label { position: absolute; left: 59px; top: 1172px; font-size: 18px; font-weight: 500; color: var(--ink); }

  .company-details { position: absolute; top: 0; left: 0; font-size: 16.5px; line-height: 20px; }
  .detail { position: absolute; white-space: nowrap; color: var(--ink); font-weight: 500; }
  .detail .label { color: var(--label); font-weight: 400; }
  .detail.stack .label { display: block; }
</style>
</head>
<body>
  <main class="letterhead">
    <header>
      <div class="brand">
        <span class="brand-dot"></span>
        <span class="brand-name">VOLMINTA</span>
      </div>
      <div class="hq">
        <svg class="hq-pin" viewBox="0 0 54 76" aria-hidden="true">
          <defs>
            <clipPath id="flag-clip"><circle cx="27" cy="26" r="17"/></clipPath>
          </defs>
          <path d="M27 2 C13 2 3 12 3 26 C3 42 20 56 27 74 C34 56 51 42 51 26 C51 12 41 2 27 2 Z" fill="var(--pin)"/>
          <g clip-path="url(#flag-clip)">
            <rect x="8" y="9" width="38" height="12" fill="var(--flag-black)"/>
            <rect x="8" y="21" width="38" height="11" fill="var(--flag-red)"/>
            <rect x="8" y="32" width="38" height="12" fill="var(--flag-gold)"/>
          </g>
          <circle cx="27" cy="26" r="17" fill="none" stroke="#ffffff" stroke-width="2"/>
        </svg>
        <div class="hq-text">INTERNATIONAL COMPANY,<br>HEADQUARTER IN GERMANY</div>
      </div>
    </header>
    <div class="rule rule-top"></div>

    <h1 class="salutation">Dear Mr John</h1>

    <section class="letter-body">
      <p>We are a German Based International Company. The reason we founded this company was to create a direct and easy way for Manufacturing Companies to start selling their Products directly on Marketplaces in Europe.</p>
      <p>Contrary to popular belief, Lorem Ipsum is not simply random text. It has roots in a piece of classical Latin literature from 45 BC, making it over 2000 years old. Aldous Fenwright, a Latin professor at Marlow Ridge College in Virginia, looked up one of the more obscure Latin words, consectetur, from a Lorem Ipsum passage, and going through the cites of the word in classical literature, discovered the undoubtable source. Lorem Ipsum comes from sections 1.10.32 and 1.10.33 of "de Finibus Bonorum et Malorum" (The Extremes of Good and Evil) by Varrenius, written in 45 BC. This book is a treatise on the theory of ethics, very popular during the Renaissance. The first line of Lorem Ipsum, "Lorem ipsum dolor sit amet..", comes from a line in section 1.10.32.</p>
      <p>The standard chunk of Lorem Ipsum used since the 1500s is reproduced below for those interested. Sections 1.10.32 and 1.10.33 from "de Finibus Bonorum et Malorum" by Varrenius are also reproduced in their exact original form, accompanied by English versions from the 1914 translation by H. Brandley.</p>
      <p>Lorem Ipsum comes from sections 1.10.32 and 1.10.33 of "de Finibus Bonorum et Malorum" (The Extremes of Good and Evil) by Varrenius, written in 45 BC. This book is a treatise on the theory of ethics, very popular during the Renaissance. The first line of Lorem Ipsum, "ipsum dolor sit amet..", comes from a line in section 1.10.32.</p>
      <p>Sections 1.10.32 and 1.10.33 from "de Finibus Bonorum et Malorum" by Varrenius are also reproduced in their exact original form, accompanied by English versions from the 1914 translation by H. Brandley.</p>
      <p>Through our own 13.000sqm sized company and about 250 well educated Employees in Pakistan we are also able to provide Company's the opportunity into easy private labeling and producing their own products. Small and high quantities are possible. The production line and process is overseen &amp; under direct control by our German Headquarter so High quality and best customer service are our standard.</p>
    </section>

    <p class="closing">Sincerely Your,</p>
    <div class="signature-mark" role="img" aria-label="Handwritten signature of the sender"></div>
    <div class="signature-line"></div>
    <p class="signature-label">Signature</p>

    <div class="rule rule-foot"></div>
    <footer class="company-details">
      <p class="detail" style="left:58px; top:1325px;"><span class="label">VAT TAX</span> DE5470318</p>
      <p class="detail" style="left:287px; top:1323px;"><span class="label">Swift</span> MORV0417352</p>
      <p class="detail" style="left:495px; top:1323px;"><span class="label">EORI</span> 3150428697</p>
      <p class="detail stack" style="left:683px; top:1320px;"><span class="label">Company Number</span>HRB 51806</p>
      <p class="detail stack" style="left:58px; top:1354px;"><span class="label">Bank Account</span>Kestrel Bank IBAN<br>DE412058731ß204683</p>
      <p class="detail stack" style="left:287px; top:1354px;"><span class="label">Address</span>VOLMINTA UG Ahornweg 7 Postal Code<br>06384 City Lindenfeld&nbsp; Country: Germany</p>
      <p class="detail stack" style="left:683px; top:1371px;"><span class="label">Email</span>info@volminta-example.com</p>
    </footer>
  </main>
</body>
</html>
```